BRN website video quote promotion tiles

We are promoting vehicle leasing by video, which contains several quotation examples imported from the video. We must re-vamp the quotation tiles, contact boxes, and contact form. The first tile is generated from the video, so this must be a separate project. We are looking for a welcoming, professional flow and leave color choices to design with an emphasis on communication prompts, and additional prompts in the design would be welcome.

Target Market(s)

Any Customer interaction from the tile quotes, contact, call, message,

Industry/Entity Type

vehicle leasing

Coding

Coded - Design and coding required

Number of Pages Required

1 page

Colors

Designer to choose colors to be used in the design.

Requirements
Must have
• emphasis on point of contact and visual impact on quote tile excluding main one
Should not have
• changes to the quote structure as these imported from video pricing no changes to main image as this template which can addressed as separate project

```html
<!DOCTYPE html>
<html lang="en">
<head>
<meta charset="UTF-8">
<title>BRN Quote Tiles</title>
<link href="https://fonts.googleapis.com/css2?family=Quicksand:wght@400;500;600;700&family=Playfair+Display:wght@400;500&display=swap" rel="stylesheet">
<style>
  :root {
    --bg: #d6d6d6;
    --orange: #d4772f;
    --ink: #161616;
    --ink-soft: #2a2a2a;
    --tile-white: #ffffff;
    --card: #ebebeb;
    --card-edge: #cfcfcf;
    --chip: #ffffff;
    --form-dark: #111111;
    --form-line: rgba(255,255,255,0.55);
  }
  * { box-sizing: border-box; margin: 0; padding: 0; }
  html, body { width: 1200px; height: 723px; overflow: hidden; background: var(--bg); }
  body { position: relative; font-family: "Quicksand", sans-serif; color: var(--ink); }

  .panel { position: absolute; width: 532px; height: 295px; }
  .panel--form { left: 50.6px; top: 49.7px; }
  .panel--wide { left: 617.6px; top: 49.7px; background: var(--tile-white); }
  .panel--stacked { left: 50.6px; top: 378.5px; background: var(--tile-white); }
  .panel--side { left: 617.6px; top: 378.5px; background: var(--tile-white); }

  /* contact form */
  .form-backdrop {
    position: absolute; inset: 0;
    background:
      radial-gradient(ellipse at 50% 20%, #2c2a27 0%, transparent 60%),
      linear-gradient(180deg, #1d1c1b 0%, #141414 55%, #0c0c0c 100%);
  }
  .form-frame {
    position: absolute; left: 21.4px; top: 36.5px; width: 488px; height: 234px;
    border: 1px solid var(--form-line); border-radius: 10px;
  }
  .form-title {
    position: absolute; left: 0; right: 0; top: 28px; text-align: center;
    font-size: 11.4px; font-weight: 600; color: #fff; letter-spacing: 0.2px;
  }
  .form-title span { background: #181717; padding: 0 6px; }
  .form-title em { font-style: normal; color: var(--orange); }
  .field {
    position: absolute; height: 24px;
    border: 1px solid var(--form-line); border-radius: 3px;
  }
  .field-label {
    position: absolute; left: 10px; top: -5px; padding: 0 5px;
    font-size: 7px; font-weight: 500; color: #fff; background: #161616; line-height: 9px;
  }
  .field-icon { position: absolute; right: 12px; top: 7px; width: 9px; height: 9px; color: #fff; }
  .field--name { left: 48.2px; top: 66px; width: 206px; }
  .field--email { left: 278px; top: 66px; width: 206px; }
  .field--phone { left: 48.2px; top: 114px; width: 436px; }
  .field--message { left: 48.2px; top: 161px; width: 436px; height: 49px; }
  .send-button {
    position: absolute; left: 213px; top: 233px; width: 106px; height: 19px;
    background: var(--orange); border-radius: 10px; color: #fff;
    font-size: 7px; font-weight: 600; text-align: center; line-height: 19px;
  }

  /* quote cards */
  .card {
    position: absolute; left: 6px; top: 8px; width: 520px; height: 279px;
    border: 1px solid var(--card-edge); border-radius: 20px;
    background:
      linear-gradient(120deg, transparent 40%, rgba(255,255,255,0.55) 48%, transparent 56%),
      linear-gradient(135deg, #e4e4e4 0%, #eeeeee 50%, #e2e2e2 100%);
    overflow: hidden;
  }
  .abs { position: absolute; }
  .centered { left: 0; right: 0; text-align: center; }
  .heading-caps { font-weight: 600; font-size: 23px; letter-spacing: 0.5px; }
  .heading-serif { font-family: "Playfair Display", serif; font-size: 27px; }
  .accent { color: var(--orange); }
  .terms-line { font-family: "Playfair Display", serif; font-size: 20px; }
  .servicing { font-size: 11px; font-weight: 500; color: var(--ink-soft); }
  .tagline-caps { font-size: 12.6px; font-weight: 600; letter-spacing: 0.2px; }
  .tagline { font-size: 17px; font-weight: 500; }

  .price {
    position: absolute; width: 115px; height: 32px; background: var(--orange);
    border-radius: 3px; color: #fff; display: flex; align-items: center; justify-content: center;
    font-size: 13px; font-weight: 600; gap: 4px;
  }
  .price small { font-size: 7.5px; font-weight: 600; padding-top: 3px; }
  .price--vertical {
    width: 38px; height: 115px; flex-direction: column;
  }
  .price--vertical .price-text { transform: rotate(90deg); white-space: nowrap; display: flex; align-items: center; gap: 4px; }

  .action {
    position: absolute; width: 39px; height: 32px; background: var(--orange);
    border-radius: 3px; display: flex; align-items: center; justify-content: center; color: #fff;
  }
  .action svg { width: 22px; height: 22px; }

  .chip {
    position: absolute; height: 32px; background: var(--chip); border-radius: 3px;
    font-family: "Playfair Display", serif; font-size: 15.5px;
    display: flex; align-items: center; justify-content: center;
  }
  .divider { position: absolute; height: 0; border-top: 1px dotted #a99a86; }

  .vertical-title {
    position: absolute; left: 37px; top: 146px;
    transform: translate(-50%, -50%) rotate(-90deg);
    font-family: "Playfair Display", serif; font-size: 40px; white-space: nowrap; line-height: 1;
  }
</style>
</head>
<body>

<svg width="0" height="0" style="position:absolute">
  <defs>
    <symbol id="icon-quote" viewBox="0 0 24 24" fill="none" stroke="currentColor" stroke-width="1.4" stroke-linecap="round" stroke-linejoin="round">
      <path d="M3 6h12v11H8l-3 3v-3H3z"/>
      <path d="M5.5 9.5h7M5.5 12h7M5.5 14.5h4"/>
      <path d="M14 13l7-9 1.5 1.2-7 9-2 .8z"/>
    </symbol>
    <symbol id="icon-call" viewBox="0 0 24 24" fill="none" stroke="currentColor" stroke-width="1.5" stroke-linecap="round" stroke-linejoin="round">
      <circle cx="12" cy="12" r="9.5"/>
      <path d="M9 7.5l1.3 2.6-1 1c.6 1.4 1.6 2.4 3 3l1-1 2.6 1.3-.6 1.8c-3.6.2-7.3-3.5-7.1-7.1z"/>
    </symbol>
    <symbol id="icon-user" viewBox="0 0 12 12" fill="none" stroke="currentColor" stroke-width="1"><circle cx="6" cy="4" r="2.3"/><path d="M2 11c0-2.4 1.8-4 4-4s4 1.6 4 4"/></symbol>
    <symbol id="icon-mail" viewBox="0 0 12 12" fill="none" stroke="currentColor" stroke-width="1"><rect x="1" y="2.5" width="10" height="7"/><path d="M1 2.5l5 4 5-4M1 9.5l3.5-3.5M11 9.5L7.5 6"/></symbol>
    <symbol id="icon-phone" viewBox="0 0 12 12" fill="none" stroke="currentColor" stroke-width="1"><path d="M2.5 1.5l2 .3.7 2.2-1.2.9c.6 1.3 1.6 2.3 2.9 2.9l.9-1.2 2.2.7.3 2c-4.5.8-8.6-3.3-7.8-7.8z"/></symbol>
    <symbol id="icon-message" viewBox="0 0 12 12" fill="none" stroke="currentColor" stroke-width="1"><path d="M1.5 2h9v6H4.5L2 10V8h-.5z"/><path d="M3.5 4.2h5M3.5 5.8h3.5"/></symbol>
  </defs>
</svg>

<!-- Contact form -->
<section class="panel panel--form">
  <div class="form-backdrop" role="img" aria-label="Dusk photograph of a car on a road with wind turbines on the hills"></div>
  <div class="form-frame"></div>
  <h2 class="form-title"><span>PLEASE SUBMIT <em>YOUR CONTACT DETAILS</em></span></h2>
  <div class="field field--name"><span class="field-label">YOUR NAME</span><svg class="field-icon"><use href="#icon-user"/></svg></div>
  <div class="field field--email"><span class="field-label">EMAIL ADDRESS</span><svg class="field-icon"><use href="#icon-mail"/></svg></div>
  <div class="field field--phone"><span class="field-label">CONTACT NUMBER</span><svg class="field-icon"><use href="#icon-phone"/></svg></div>
  <div class="field field--message"><span class="field-label">TYPE YOUR MESSAGE</span><svg class="field-icon"><use href="#icon-message"/></svg></div>
  <div class="send-button">SEND YOUR MESSAGE</div>
</section>

<!-- Wide quote tile -->
<section class="panel panel--wide">
  <div class="card">
    <h2 class="abs centered heading-caps" style="top:33px"><span class="accent">CONTRACT</span> HIRE</h2>
    <p class="abs centered terms-line" style="top:78px"><span class="accent">3</span> Years, <span class="accent">9+35</span>, <span class="accent">6K</span> Miles Annually</p>
    <p class="abs centered servicing" style="top:127px">Complete Servicing and Maintenance included</p>
    <p class="abs centered tagline-caps" style="top:167px">NORTHWAY LEASING LET’S WORK TOGETHER</p>
    <div class="price" style="left:21px;top:210px">£249.27 <small>PLUS VAT</small></div>
    <div class="divider" style="left:154px;top:225px;width:237px"></div>
    <div class="action" style="left:407px;top:210px"><svg><use href="#icon-quote"/></svg></div>
    <div class="action" style="left:462px;top:210px"><svg><use href="#icon-call"/></svg></div>
  </div>
</section>

<!-- Stacked quote tile -->
<section class="panel panel--stacked">
  <div class="card">
    <h2 class="abs centered heading-serif" style="top:20px"><span class="accent">Contract</span> Hire</h2>
    <div class="price" style="left:201px;top:75px">£249.27 <small>PLUS VAT</small></div>
    <div class="chip" style="left:71px;top:132px;width:91px"><span class="accent">3</span>&nbsp;Years</div>
    <div class="chip accent" style="left:182px;top:132px;width:91px">9+35</div>
    <div class="chip" style="left:294px;top:132px;width:153px"><span class="accent">6K</span>&nbsp;Miles Annually</div>
    <p class="abs centered servicing" style="top:187px">Complete Servicing and Maintenance included</p>
    <p class="abs centered tagline" style="top:222px">Northway Leasing Let’s work together</p>
    <div class="action" style="left:20px;top:230px"><svg><use href="#icon-quote"/></svg></div>
    <div class="action" style="left:460px;top:230px"><svg><use href="#icon-call"/></svg></div>
  </div>
</section>

<!-- Side-title quote tile -->
<section class="panel panel--side">
  <div class="card">
    <h2 class="vertical-title"><span class="accent">Contract</span> Hire</h2>
    <div class="chip" style="left:71px;top:85px;width:91px"><span class="accent">3</span>&nbsp;Years</div>
    <div class="chip accent" style="left:183px;top:85px;width:91px">9+35</div>
    <div class="chip" style="left:295px;top:85px;width:153px"><span class="accent">6K</span>&nbsp;Miles Annually</div>
    <p class="abs servicing" style="left:0;width:520px;text-align:center;top:143px;padding-left:0">Complete Servicing and Maintenance included</p>
    <p class="abs tagline" style="left:0;width:520px;text-align:center;top:182px">Northway Leasing Let’s work together</p>
    <div class="price price--vertical" style="left:471px;top:35px"><span class="price-text">£249.27 <small>PLUS VAT</small></span></div>
    <div class="action" style="left:471px;top:166px"><svg><use href="#icon-quote"/></svg></div>
    <div class="action" style="left:471px;top:212px"><svg><use href="#icon-call"/></svg></div>
  </div>
</section>

</body>
</html>
```